Read Your Frame
Stationary
Project: Read Your Frame
Read Your Frame - Health
Creative Brief
Use specific fonts
Whatever fonts look best!
Professional
Linus Ferrick
Body Composition Specialist/ Personal Trainer
Dont put address.
linusferrick@mailvex.com
ReadYourFrameMakeup.com
We use a state of the art body composition analyzer to accurately determine total body fat, essential fat, non essential fat, reserve fat, total body water, and lean mass. It's fast, non-invasive, and comparable to the Gold Standard. To find out more visit our website or call us.

```html
<!DOCTYPE html>
<html lang="en">
<head>
<meta charset="utf-8">
<title>Read Your Frame — Business Cards</title>
<link rel="stylesheet" href="https://fonts.googleapis.com/css2?family=Arimo:wght@400;700&display=swap">
<style>
  :root {
    --page: #e9e9e6;
    --card-light: #ffffff;
    --card-dark: #0d0d0f;
    --ink-dark: #2a2a2a;
    --ink-light: #e6e6e6;
    --muted: #7a7a7a;
    --blue: #2b8fd6;
    --blue-soft: #58b2ef;
    --rule-light: #c9c9c9;
    --rule-dark: #3a3a3a;
  }
  * { box-sizing: border-box; margin: 0; padding: 0; }
  html, body { width: 1200px; height: 911px; overflow: hidden; }
  body {
    background: var(--page);
    font-family: "Arimo", Arial, sans-serif;
    position: relative;
  }
  .card {
    position: absolute;
    width: 520px;
    height: 300px;
    border-radius: 14px;
    overflow: hidden;
    box-shadow: 0 6px 18px rgba(0,0,0,0.18);
  }
  .card--light { background: var(--card-light); color: var(--ink-dark); }
  .card--dark  { background: linear-gradient(160deg, #1d1d21 0%, var(--card-dark) 60%); color: var(--ink-light); }
  .pos-a { left: 60px;  top: 130px; }
  .pos-b { left: 620px; top: 130px; }
  .pos-c { left: 60px;  top: 490px; }
  .pos-d { left: 620px; top: 490px; }

  /* front */
  .brand {
    position: absolute; left: 34px; top: 108px; width: 200px;
  }
  .brand__name {
    display: flex; align-items: center; gap: 8px;
    font-weight: 700; font-size: 26px; letter-spacing: -0.5px;
  }
  .card--light .brand__name { color: var(--blue); }
  .card--dark .brand__name  { color: var(--blue-soft); }
  .brand__mark { width: 14px; height: 14px; border-radius: 50%; background: currentColor; flex: none; }
  .brand__tagline {
    margin-top: 6px; font-size: 11px; line-height: 1.25; color: var(--blue); font-weight: 700;
  }
  .divider {
    position: absolute; left: 250px; top: 56px; width: 1px; height: 130px;
  }
  .card--light .divider { background: var(--rule-light); }
  .card--dark .divider  { background: var(--rule-dark); }
  .contact { position: absolute; left: 266px; top: 62px; }
  .contact__name { font-size: 21px; color: var(--blue); margin-bottom: 4px; }
  .contact__role { font-size: 11px; line-height: 1.35; margin-bottom: 18px; }
  .contact__line { font-size: 10.5px; line-height: 1.5; }
  .website {
    position: absolute; right: 30px; bottom: 26px; font-size: 11px; color: var(--blue);
  }

  /* back */
  .figure {
    position: absolute; left: 0; top: 0; width: 150px; height: 300px;
  }
  .card--light .figure { background: linear-gradient(90deg, #dcdcdc, #f4f4f4 80%, transparent); }
  .card--dark .figure  { background: linear-gradient(90deg, #26262b, #141417 80%, transparent); }
  .pitch { position: absolute; left: 160px; top: 44px; width: 320px; }
  .pitch__body { font-size: 14.5px; line-height: 1.35; }
  .pitch__cta { margin-top: 18px; font-size: 14.5px; font-weight: 700; color: var(--blue); }
</style>
</head>
<body>

  <!-- light front -->
  <section class="card card--light pos-a">
    <div class="brand">
      <div class="brand__name"><span class="brand__mark"></span>Read Your Frame</div>
      <p class="brand__tagline">Look great.<br>Feel great.<br>Do great things.</p>
    </div>
    <div class="divider"></div>
    <div class="contact">
      <p class="contact__name">Linus Ferrick</p>
      <p class="contact__role">Body Composition Specialist<br>Personal Trainer</p>
      <p class="contact__line">Phone&nbsp; 615.555.0142</p>
      <p class="contact__line">Email&nbsp;&nbsp; linusferrick@mailvex.com</p>
    </div>
    <p class="website">www.ReadYourFrameMakeup.com</p>
  </section>

  <!-- dark front -->
  <section class="card card--dark pos-b">
    <div class="brand">
      <div class="brand__name"><span class="brand__mark"></span>Read Your Frame</div>
      <p class="brand__tagline">Look great.<br>Feel great.<br>Do great things.</p>
    </div>
    <div class="divider"></div>
    <div class="contact">
      <p class="contact__name">Linus Ferrick</p>
      <p class="contact__role">Body Composition Specialist<br>Personal Trainer</p>
      <p class="contact__line">Phone&nbsp; 615.555.0142</p>
      <p class="contact__line">Email&nbsp;&nbsp; linusferrick@mailvex.com</p>
    </div>
    <p class="website">www.ReadYourFrameMakeup.com</p>
  </section>

  <!-- light back -->
  <section class="card card--light pos-c">
    <div class="figure" role="img" aria-label="Faint silhouette of a standing person"></div>
    <div class="pitch">
      <p class="pitch__body">We use a state of the art body composition analyzer to accurately determine total body fat, essential fat, non essential fat, reserve fat, total body water, and lean mass. It's fast, non-invasive, and comparable to the Gold Standard.</p>
      <p class="pitch__cta">To find out more visit our website or call us</p>
    </div>
    <p class="website">www.ReadYourFrameMakeup.com</p>
  </section>

  <!-- dark back -->
  <section class="card card--dark pos-d">
    <div class="figure" role="img" aria-label="Faint silhouette of a standing person"></div>
    <div class="pitch">
      <p class="pitch__body">We use a state of the art body composition analyzer to accurately determine total body fat, essential fat, non essential fat, reserve fat, total body water, and lean mass. It's fast, non-invasive, and comparable to the Gold Standard.</p>
      <p class="pitch__cta">To find out more visit our website or call us</p>
    </div>
    <p class="website">www.ReadYourFrameMakeup.com</p>
  </section>

</body>
</html>
```